Rack Card for Bright Meadow Dog Training

I love the logo you designed for me a while back (I had it updated and have the new files).

I need a rack card designed, 2 sided.

One side will be Bright Meadow Dog Training (my general dog training business)

The other side will be my Deaf and Blind Dog Training Business speciality.

Both sides Full Color/4 color

3.5 x 8.5 inches

I can provide photos and text accordingly.

Let me know the estimated price and Turn around time.

```html
<!DOCTYPE html>
<html lang="en">
<head>
<meta charset="utf-8">
<title>Bright Meadow Dog Training – Rack Card</title>
<link rel="stylesheet" href="https://fonts.googleapis.com/css2?family=Poppins:wght@400;500;600;700;800&display=swap">
<style>
  :root {
    --orange: #f7941d;
    --ink: #1a1a1a;
    --dark: #231f20;
    --black: #0d0d0d;
    --white: #ffffff;
    --cell: #3a3a3a;
    --stage: #eceef1;
  }
  * { margin: 0; padding: 0; box-sizing: border-box; }
  html, body { width: 1200px; height: 2223px; overflow: hidden; }
  body { background: var(--stage); font-family: "Poppins", sans-serif; position: relative; }

  .card { position: absolute; top: 456px; width: 540px; height: 1311px; overflow: hidden;
          box-shadow: 0 18px 40px rgba(0,0,0,.25); }
  .card--general { left: 30px; background: var(--white); }
  .card--special { left: 630px; background: var(--black); }
  .card svg.bg { position: absolute; inset: 0; }
  .abs { position: absolute; }

  /* general side */
  .brand-top { left: 30px; top: 28px; font-size: 34px; font-weight: 800; color: var(--ink); line-height: 1; letter-spacing: -.5px; }
  .brand-dog { left: 26px; top: 62px; font-size: 92px; font-weight: 800; color: var(--ink); line-height: 1; letter-spacing: -3px; }
  .brand-training { left: 28px; top: 150px; font-size: 48px; font-weight: 800; color: var(--orange); line-height: 1; }
  .logo-name { font-weight: 600; font-size: 22px; color: var(--ink); text-align: center; line-height: 1.15; }

  .service-label { top: 862px; width: 120px; text-align: center; font-size: 18px; font-weight: 600; line-height: 1.25; color: var(--white); }
  .service-label span { display: block; color: var(--orange); }

  .offer-pill { left: 33px; top: 936px; width: 264px; height: 33px; border-radius: 17px; background: var(--orange);
                color: var(--dark); font-weight: 700; font-size: 19px; text-align: center; line-height: 33px; }
  .offer-list { list-style: none; color: var(--white); font-size: 19px; line-height: 30px; }
  .offer-list li { position: relative; padding-left: 40px; }
  .offer-list li.cont { padding-left: 40px; }
  .offer-list svg { position: absolute; left: 2px; top: 6px; }

  .cta-rule { left: 33px; top: 1142px; width: 482px; height: 3px; background: var(--orange); }
  .cta-pill { left: 122px; top: 1108px; width: 302px; height: 66px; border-radius: 33px; background: var(--white);
              text-align: center; font-size: 17px; font-weight: 500; line-height: 22px; padding-top: 11px; color: var(--ink); }
  .cta-pill b { color: var(--orange); font-weight: 700; }

  .areas { left: 35px; top: 1186px; font-size: 15px; font-weight: 700; color: var(--white); line-height: 21px; }
  .areas span { color: var(--orange); }

  .site { left: 0; width: 540px; top: 1262px; text-align: center; font-size: 23px; font-weight: 500; color: var(--white); letter-spacing: .5px; }
  .site span { color: var(--orange); }

  /* specialty side */
  .trainer-band { left: 230px; top: 0; width: 310px; height: 98px; background: rgba(50,50,50,.82); }
  .trainer-name { right: 28px; top: 24px; font-size: 29px; font-weight: 600; color: var(--white); text-align: right; }
  .trainer-role { right: 28px; top: 64px; font-size: 14px; letter-spacing: 4px; color: var(--white); }

  .special-title { left: 0; width: 540px; top: 490px; text-align: center; font-size: 46px; font-weight: 800; line-height: 46px; color: var(--white); }
  .special-title span { display: block; color: var(--orange); }

  .topic h3 { font-size: 17px; font-weight: 700; color: var(--orange); margin-bottom: 4px; }
  .topic p { font-size: 16.5px; line-height: 20px; color: var(--white); }

  .consult { left: 0; width: 540px; top: 1124px; text-align: center; font-size: 17px; font-weight: 500; color: var(--white); }
  .consult b { color: var(--orange); font-weight: 700; }

  .phones { left: 77px; top: 1160px; width: 386px; border: 3px solid #4a4a4a; border-radius: 8px; border-collapse: separate; border-spacing: 3px; background: #4a4a4a; }
  .phones td { height: 37px; padding: 0 10px; }
  .phones .region { background: var(--cell); color: #e5e5e5; font-size: 16px; width: 152px; }
  .phones .number { background: var(--orange); color: var(--white); font-size: 20px; font-weight: 500; text-align: center; }
</style>
</head>
<body>

<!-- General training side -->
<section class="card card--general" aria-label="Bright Meadow Dog Training rack card front">
  <svg class="bg" width="540" height="1311" viewBox="0 0 540 1311">
    <defs>
      <linearGradient id="heroTone" x1="0" y1="0" x2="1" y2="1">
        <stop offset="0" stop-color="#8d9187"/>
        <stop offset=".45" stop-color="#d4a86b"/>
        <stop offset="1" stop-color="#9a8a72"/>
      </linearGradient>
      <linearGradient id="tone1" x1="0" y1="0" x2="0" y2="1"><stop offset="0" stop-color="#e9d7b4"/><stop offset="1" stop-color="#6f8f4a"/></linearGradient>
      <linearGradient id="tone2" x1="0" y1="0" x2="0" y2="1"><stop offset="0" stop-color="#a37a45"/><stop offset="1" stop-color="#e2e2de"/></linearGradient>
      <linearGradient id="tone3" x1="0" y1="0" x2="1" y2="1"><stop offset="0" stop-color="#3d5a95"/><stop offset="1" stop-color="#7b6a55"/></linearGradient>
      <linearGradient id="tone4" x1="0" y1="0" x2="0" y2="1"><stop offset="0" stop-color="#b8b8b6"/><stop offset="1" stop-color="#8f8f8c"/></linearGradient>
    </defs>
    <path d="M0 725 C150 700 380 690 540 640 V1311 H0 Z" fill="var(--dark)"/>
    <path role="img" aria-label="Photo of a golden retriever lying indoors beside a potted plant"
          d="M205 330 C300 240 450 225 540 245 V690 C420 705 250 710 40 705 C40 560 105 430 205 330 Z" fill="url(#heroTone)"/>
    <path d="M150 430 C220 300 360 240 480 245" fill="none" stroke="var(--black)" stroke-width="10" stroke-linecap="round"/>
    <path d="M320 700 C420 690 500 665 540 640" fill="none" stroke="var(--black)" stroke-width="8"/>
    <circle cx="450" cy="115" r="100" fill="var(--white)" stroke="var(--black)" stroke-width="6"/>
    <circle role="img" aria-label="Photo of a puppy on grass" cx="91" cy="775" r="66" fill="url(#tone1)" stroke="var(--white)" stroke-width="3"/>
    <circle role="img" aria-label="Photo of an adult shepherd dog" cx="205" cy="775" r="66" fill="url(#tone2)" stroke="var(--white)" stroke-width="3"/>
    <circle role="img" aria-label="Photo of a rescue dog with its handler" cx="326" cy="775" r="66" fill="url(#tone3)" stroke="var(--white)" stroke-width="3"/>
    <circle role="img" aria-label="Photo of a dog on a sofa" cx="448" cy="760" r="66" fill="url(#tone4)" stroke="var(--white)" stroke-width="3"/>
  </svg>

  <div class="abs brand-top">BRIGHT MEADOW</div>
  <div class="abs brand-dog">DOG</div>
  <div class="abs brand-training">TRAINING</div>
  <div class="abs logo-name" style="left:370px; top:88px; width:160px;">Bright<br>Meadow</div>

  <div class="abs service-label" style="left:31px;">PUPPY<span>TRAINING</span></div>
  <div class="abs service-label" style="left:145px;">ADULT DOG<span>TRAINING</span></div>
  <div class="abs service-label" style="left:266px;">RESCUE<span>DOGS</span></div>
  <div class="abs service-label" style="left:386px;">BEHAVIORAL<span>ISSUES</span></div>

  <div class="abs offer-pill">SERVICES WE OFFER</div>
  <ul class="abs offer-list" style="left:33px; top:980px;">
    <li><svg width="20" height="18" viewBox="0 0 20 18"><g fill="var(--orange)"><ellipse cx="10" cy="13" rx="5" ry="4"/><circle cx="4" cy="7" r="2.2"/><circle cx="8" cy="3.5" r="2.2"/><circle cx="12.5" cy="3.5" r="2.2"/><circle cx="16.5" cy="7" r="2.2"/></g></svg>Puppy Training</li>
    <li><svg width="20" height="18" viewBox="0 0 20 18"><g fill="var(--orange)"><ellipse cx="10" cy="13" rx="5" ry="4"/><circle cx="4" cy="7" r="2.2"/><circle cx="8" cy="3.5" r="2.2"/><circle cx="12.5" cy="3.5" r="2.2"/><circle cx="16.5" cy="7" r="2.2"/></g></svg>House Breaking</li>
    <li><svg width="20" height="18" viewBox="0 0 20 18"><g fill="var(--orange)"><ellipse cx="10" cy="13" rx="5" ry="4"/><circle cx="4" cy="7" r="2.2"/><circle cx="8" cy="3.5" r="2.2"/><circle cx="12.5" cy="3.5" r="2.2"/><circle cx="16.5" cy="7" r="2.2"/></g></svg>Leash Training</li>
    <li><svg width="20" height="18" viewBox="0 0 20 18"><g fill="var(--orange)"><ellipse cx="10" cy="13" rx="5" ry="4"/><circle cx="4" cy="7" r="2.2"/><circle cx="8" cy="3.5" r="2.2"/><circle cx="12.5" cy="3.5" r="2.2"/><circle cx="16.5" cy="7" r="2.2"/></g></svg>Obedience</li>
  </ul>
  <ul class="abs offer-list" style="left:263px; top:975px; line-height:25px;">
    <li><svg width="20" height="18" viewBox="0 0 20 18"><g fill="var(--orange)"><ellipse cx="10" cy="13" rx="5" ry="4"/><circle cx="4" cy="7" r="2.2"/><circle cx="8" cy="3.5" r="2.2"/><circle cx="12.5" cy="3.5" r="2.2"/><circle cx="16.5" cy="7" r="2.2"/></g></svg>Rescue Dog</li>
    <li class="cont" style="margin-bottom:6px;">Training</li>
    <li style="margin-bottom:6px;"><svg width="20" height="18" viewBox="0 0 20 18"><g fill="var(--orange)"><ellipse cx="10" cy="13" rx="5" ry="4"/><circle cx="4" cy="7" r="2.2"/><circle cx="8" cy="3.5" r="2.2"/><circle cx="12.5" cy="3.5" r="2.2"/><circle cx="16.5" cy="7" r="2.2"/></g></svg>Separation Anxiety</li>
    <li class="cont">Socialization</li>
  </ul>

  <div class="abs cta-rule"></div>
  <div class="abs cta-pill">SCHEDULE <b>FREE 15 MINUTE</b><br>PHONE CONSULTATION</div>

  <div class="abs areas"><span>DOG TRAINING IN</span><br>REDONDO BEACH, MANHATTAN BEACH, SOUTH BAY,<br>LONG BEACH, THE WEST SIDE</div>

  <div class="abs site">www.<span>brightmeadowdogtraining</span>.com</div>
</section>

<!-- Deaf & blind specialty side -->
<section class="card card--special" aria-label="Deaf and blind dog training rack card back">
  <svg class="bg" width="540" height="1311" viewBox="0 0 540 1311">
    <defs>
      <linearGradient id="trainerTone" x1="0" y1="0" x2="1" y2="1">
        <stop offset="0" stop-color="#6e6a5c"/>
        <stop offset=".5" stop-color="#8c6a45"/>
        <stop offset="1" stop-color="#cfc8bd"/>
      </linearGradient>
      <linearGradient id="tone5" x1="0" y1="0" x2="1" y2="1"><stop offset="0" stop-color="#c77a3a"/><stop offset="1" stop-color="#5f7a3f"/></linearGradient>
      <linearGradient id="tone6" x1="0" y1="0" x2="1" y2="1"><stop offset="0" stop-color="#2f4a2a"/><stop offset="1" stop-color="#5a3424"/></linearGradient>
      <linearGradient id="tone7" x1="0" y1="0" x2="1" y2="1"><stop offset="0" stop-color="#d9d9d9"/><stop offset="1" stop-color="#2b2b2b"/></linearGradient>
    </defs>
    <path role="img" aria-label="Photo of the lead trainer seated with her dogs at home"
          d="M0 0 H540 V275 C390 430 170 470 0 400 Z" fill="url(#trainerTone)"/>
    <path d="M0 400 C170 470 390 430 540 275 V305 C390 465 160 505 0 440 Z" fill="var(--orange)"/>
    <circle cx="422" cy="368" r="90" fill="var(--white)" stroke="var(--black)" stroke-width="5"/>
    <circle role="img" aria-label="Photo of a shiba dog learning a hand signal" cx="112" cy="668" r="72" fill="url(#tone5)" stroke="var(--white)" stroke-width="3"/>
    <circle role="img" aria-label="Photo of a brown dog being guided by touch" cx="430" cy="812" r="72" fill="url(#tone6)" stroke="var(--white)" stroke-width="3"/>
    <circle role="img" aria-label="Photo of a husky wearing a muzzle" cx="115" cy="995" r="72" fill="url(#tone7)" stroke="var(--white)" stroke-width="3"/>
  </svg>

  <div class="abs trainer-band"></div>
  <div class="abs trainer-name">Laura Hensley</div>
  <div class="abs trainer-role">LEAD TRAINER</div>

  <div class="abs logo-name" style="left:342px; top:341px; width:160px;">Bright<br>Meadow</div>

  <h1 class="abs special-title">DEAF &amp; BLIND<span>DOG TRAINING</span></h1>

  <div class="abs topic" style="left:207px; top:604px; width:310px;">
    <h3>DEAF DOG TRAINING</h3>
    <p>Deaf dogs can easily be trained using hand signals.<br>We owe it to our dogs to teach them how to behave, and that the world is a safe place.</p>
  </div>
  <div class="abs topic" style="left:37px; top:779px; width:300px;">
    <h3>BLIND DOG TRAINING</h3>
    <p>Blind dogs can easily be trained using touch and tactile cues.<br>We owe it to our dogs to teach them how to behave, and that the world is a safe place.</p>
  </div>
  <div class="abs topic" style="left:207px; top:965px; width:315px;">
    <h3>DEAF/ BLIND DOG TRAINING</h3>
    <p>Training a dog that is both blind and deaf can come with its own challenges, we have many years of experience to help.</p>
  </div>

  <div class="abs consult">SCHEDULE <b>FREE 15 MINUTE</b> PHONE CONSULTATION</div>
  <table class="abs phones">
    <tr><td class="region">Los Angeles</td><td class="number">(310) 555-0147</td></tr>
    <tr><td class="region">Orange Country</td><td class="number">(714) 555-0182</td></tr>
  </table>

  <div class="abs site">www.<span>brightmeadowdogtraining</span>.com</div>
</section>

</body>
</html>
```